Kestrelbrook Student Accomodation needs a business card design

Hi Guys,

We are a Student Accommodation company in Australia. We already have a logo which I will submit.

I will require the design of the business cards from you.

I am after something that looks clean, modern and that people feel interested and actually want to contact us.

We would like to see designs that are innovative.

On the business cards I will require to have:

Employee Name
Position
Phone number
Email
plain square page

I hope you can help me with this project guys as I have heard really good things from you.

```html
<!DOCTYPE html>
<html lang="en">
<head>
<meta charset="utf-8">
<title>Kestrelbrook Student Accomodation – Business Card</title>
<link rel="stylesheet" href="https://fonts.googleapis.com/css2?family=Arimo:wght@400;700&display=swap">
<style>
  :root {
    --green: #0a8a17;
    --green-dark: #066e10;
    --green-light: #1a9a24;
    --gold: #ecae22;
    --paper: #f4f4f4;
    --paper-shade: #e6e6e6;
    --ink: #5a5a5a;
    --backdrop: #9b9b9b;
  }
  * { box-sizing: border-box; margin: 0; padding: 0; }
  html, body { width: 1200px; height: 720px; overflow: hidden; }
  body {
    background: var(--backdrop);
    font-family: "Arimo", Arial, sans-serif;
    position: relative;
  }
  .card {
    position: absolute;
    top: 205px;
    width: 540px;
    height: 310px;
    overflow: hidden;
    box-shadow: 0 6px 18px rgba(0,0,0,.25);
  }
  .card--front { left: 40px; background: linear-gradient(160deg, #fafafa 0%, var(--paper) 55%, var(--paper-shade) 100%); }
  .card--back { left: 620px; background: linear-gradient(135deg, var(--green-light) 0%, var(--green) 50%, var(--green-dark) 100%); }

  .card__bands { position: absolute; left: 0; bottom: 0; width: 540px; height: 310px; }

  .brand {
    position: absolute;
    display: flex;
    align-items: center;
    gap: 10px;
  }
  .brand__mark { width: 26px; height: 26px; background: var(--gold); flex: none; }
  .brand__name {
    font-weight: 700;
    font-size: 19px;
    line-height: 1.15;
    text-transform: uppercase;
    letter-spacing: .5px;
  }
  .card--front .brand { left: 40px; top: 92px; }
  .card--front .brand__name { color: var(--green); }
  .card--back .brand { left: 150px; top: 120px; }
  .card--back .brand__name { color: #ffffff; }

  .contact { position: absolute; left: 280px; top: 120px; color: var(--ink); }
  .contact__name { color: var(--green); font-weight: 700; font-size: 19px; }
  .contact__role { font-size: 14px; margin-top: 3px; }
  .contact__list { list-style: none; margin-top: 20px; }
  .contact__item { display: flex; align-items: center; gap: 10px; font-size: 14px; line-height: 22px; white-space: nowrap; }
  .contact__icon { width: 13px; height: 13px; flex: none; }

  .backdrop-shape {
    position: absolute;
    background: rgba(255,255,255,.07);
  }
</style>
</head>
<body>

<section class="card card--front" aria-label="Business card, front">
  <svg class="card__bands" viewBox="0 0 540 310" aria-hidden="true">
    <polygon points="0,255 300,255 312,272 0,272" fill="var(--green)"/>
    <polygon points="320,283 540,283 540,310 335,310" fill="var(--gold)"/>
  </svg>

  <div class="brand">
    <span class="brand__mark"></span>
    <span class="brand__name">Kestrelbrook<br>Student<br>Accomodation</span>
  </div>

  <div class="contact">
    <p class="contact__name">Maya Thornton</p>
    <p class="contact__role">Chief Executive</p>
    <ul class="contact__list">
      <li class="contact__item">
        <svg class="contact__icon" viewBox="0 0 13 13" aria-hidden="true"><rect x="3" y="0.8" width="7" height="11.4" rx="1.2" fill="none" stroke="var(--green)" stroke-width="1.4"/><rect x="5.5" y="9.6" width="2" height="1.2" fill="var(--green)"/></svg>
        0400 123 987
      </li>
      <li class="contact__item">
        <svg class="contact__icon" viewBox="0 0 13 13" aria-hidden="true"><rect x="0.7" y="2.5" width="11.6" height="8" fill="var(--green)"/><polyline points="0.7,2.5 6.5,7 12.3,2.5" fill="none" stroke="#fff" stroke-width="1.2"/></svg>
        maya@kestrelbrook.com.au
      </li>
      <li class="contact__item">
        <svg class="contact__icon" viewBox="0 0 13 13" aria-hidden="true"><rect x="0.5" y="0.5" width="12" height="12" fill="var(--green)"/></svg>
        social.kestrelbrook.com.au
      </li>
    </ul>
  </div>
</section>

<section class="card card--back" aria-label="Business card, back">
  <div class="backdrop-shape" style="left:60px;top:20px;width:170px;height:170px;"></div>
  <div class="backdrop-shape" style="left:300px;top:150px;width:190px;height:190px;"></div>
  <div class="backdrop-shape" style="left:120px;top:60px;width:50px;height:50px;"></div>
  <div class="brand">
    <span class="brand__mark"></span>
    <span class="brand__name">Kestrelbrook<br>Student<br>Accomodation</span>
  </div>
</section>

</body>
</html>
```